THE PAPER HERONS - creative phenoms who raise design to high art form.

Coffee-table book format.Will feature 20 'design' companies, one from each of 20 categories:3D Design . Branding Design . Broadcast Design . Communication . Digital Design Fashion . Exhibition Design . Furniture Design . Graphic Design . Industrial Design Interior Design . Jewelry . Lighting Design . Package Design . Retail Design . Sustainable Design . Urban Design . Web Design . Yacht DesignWant an eye-catching photo(s), design, etc. This will involve some creative effort.
Updates

After some thought, decided something that is a common thread through all design industries. A nice desk, upon which is a blank sketch pad, a pencil, and beside them a computer. A designer has a new idea, uses the sketch pad, then moves on to the computer to develop his/her idea. Cheers, Gordon

Target Market(s)

US professionals who own companies involved in the world of design.

Requirements
Must have
• Format is 11 in wide and 10 inches high cover.
• Photograph(s) or artwork that will catch the eye of the
• readers browsing the book sections.

```html
<!DOCTYPE html>
<html lang="en">
<head>
<meta charset="utf-8">
<title>The Paper Herons – Book Cover</title>
<link href="https://fonts.googleapis.com/css2?family=Montserrat:wght@300;600&display=swap" rel="stylesheet">
<style>
  :root {
    --paper: #eeeeeb;
    --title-brown: #5b4f43;
    --accent-gold: #c3a371;
    --wood-light: #e9cfa8;
    --wood-mid: #d3b185;
    --wood-dark: #8c7253;
  }
  html, body {
    margin: 0;
    padding: 0;
    overflow: hidden;
    background: var(--paper);
  }
  .cover {
    position: relative;
    width: 1200px;
    height: 1091px;
    background: var(--paper);
    overflow: hidden;
    font-family: 'Montserrat', sans-serif;
  }
  .cover__block {
    position: absolute;
    left: 60px;
    right: 0;
    text-align: center;
  }
  .cover__title {
    top: 48px;
    margin: 0;
    font-weight: 300;
    font-size: 86px;
    line-height: 104px;
    letter-spacing: 3px;
    color: var(--title-brown);
  }
  .cover__subtitle {
    top: 280px;
    margin: 0;
    font-weight: 600;
    font-size: 28px;
    line-height: 40px;
    letter-spacing: 1px;
    color: var(--accent-gold);
  }
  .cover__artwork {
    position: absolute;
    left: 349px;
    top: 382px;
    width: 556px;
    height: 556px;
  }
  .cover__author {
    top: 978px;
    margin: 0;
    font-weight: 300;
    font-size: 50px;
    line-height: 64px;
    letter-spacing: 3px;
    color: var(--accent-gold);
  }
</style>
</head>
<body>
  <main class="cover">
    <h1 class="cover__block cover__title">THE PAPER<br>HERONS</h1>
    <p class="cover__block cover__subtitle">CREATIVE PHENOMS<br>WHO RAISE DESIGN TO HIGH ART FORM</p>

    <svg class="cover__artwork" viewBox="0 0 556 556" role="img" aria-label="Photograph, seen from above, of sharpened colored pencils standing in a round holder">
      <defs>
        <radialGradient id="pencil-tones" cx="50%" cy="50%" r="50%">
          <stop offset="0%" stop-color="var(--wood-light)"/>
          <stop offset="70%" stop-color="var(--wood-mid)"/>
          <stop offset="100%" stop-color="var(--wood-dark)"/>
        </radialGradient>
      </defs>
      <circle cx="278" cy="278" r="276" fill="url(#pencil-tones)"/>
    </svg>

    <p class="cover__block cover__author">GORDON HALLOWAY</p>
  </main>
</body>
</html>
```